New, modern business card for growing audiology practice

We need a new business card for our audiology practice. Our logo and website have recently changed (more modern) and we want our business cards to reflect this change.
We conduct hearing tests, perform earwax removals, and fit & dispense hearing aids to our patients. We are a family owned practice in which the owner is the one who works directly with the patient. I have attached logos in various formats to use, as well as two ideas I found on this website; as well as a scanned copy of our current logo. Good luck!

Industry/Entity Type

Business

Contact Information for Business Card

Company name: Tolvera Hearing Center
Provider name: Peter Wolstenby, Au.D. F/NSB
Phone number: (440) 683-5127
Address: 837 W. Lindell Ave. Fernbrook, OH 44390
email: tolverahearing@postvane.com
website: tolverahearing.com

Colors
000000
aaaaaa
dbdbdb
cacaca
9bcb3c
afd23c
cadf82
b1b1b1

Requirements
Must have
• My card must include information in the "details" section. In the attached images, I found a few that I liked and I would like to model after - "brisky bouncin'" and "Sound Method Center".
• Must be horizontal.
• Must include logos provided. I uploaded them in various file formats and various ways.
• Must match logo font, if possible, if not, please get as close as you can.
Nice to have
• I really like the idea of having a color on one side with just the logo and company name and the contact information and provider name on the other side. I also really like the idea of having the main color dominating on the logo/company side with accent of that same color on the contact side of the card.
Should not have
• Must not be vertical.

```html
<!DOCTYPE html>
<html lang="en">
<head>
<meta charset="utf-8">
<title>Tolvera Hearing Center – Business Card</title>
<link href="https://fonts.googleapis.com/css2?family=Lato:wght@300;400;700&display=swap" rel="stylesheet">
<style>
  :root {
    --green: #7aab3a;
    --green-light: #8cc043;
    --green-dark: #5c8f2a;
    --ink: #111111;
    --white: #ffffff;
    --paper: #f4f4f4;
    --stage: #e6e6e6;
    --grey: #aaaaaa;
  }
  * { box-sizing: border-box; margin: 0; padding: 0; }
  html, body { width: 1200px; height: 900px; overflow: hidden; }
  body {
    background: var(--stage);
    font-family: 'Lato', sans-serif;
    position: relative;
  }
  .card {
    position: absolute;
    left: 250px;
    width: 700px;
    height: 400px;
    border-radius: 22px;
    overflow: hidden;
    box-shadow: 0 6px 18px rgba(0,0,0,0.18);
  }
  /* Front: brand side */
  .card--front {
    top: 40px;
    background: linear-gradient(160deg, var(--green-light) 0%, var(--green) 50%, var(--green-dark) 100%);
  }
  .brand {
    position: absolute;
    display: flex;
    align-items: center;
    gap: 14px;
    white-space: nowrap;
  }
  .brand__mark {
    width: 26px; height: 26px;
    border-radius: 50%;
    border: 3px solid currentColor;
  }
  .brand__name {
    font-weight: 400;
    letter-spacing: 1px;
    text-transform: uppercase;
  }
  .card--front .brand {
    left: 0; right: 0; top: 172px;
    justify-content: center;
    color: var(--ink);
  }
  .card--front .brand__mark { border-color: var(--white); }
  .card--front .brand__name { font-size: 34px; }
  .front__web {
    position: absolute;
    left: 0; right: 0; bottom: 34px;
    text-align: center;
    font-size: 15px;
    letter-spacing: 0.5px;
    color: rgba(255,255,255,0.85);
  }

  /* Back: contact side */
  .card--back {
    top: 460px;
    background: linear-gradient(180deg, var(--white) 0%, var(--paper) 100%);
  }
  .card--back .brand {
    left: 0; right: 0; top: 38px;
    justify-content: center;
    color: var(--ink);
  }
  .card--back .brand__mark { border-color: var(--green); }
  .card--back .brand__name { font-size: 34px; }
  .provider {
    position: absolute;
    left: 0; right: 0; top: 100px;
    text-align: center;
  }
  .provider__name {
    display: inline-block;
    font-size: 26px;
    color: var(--ink);
    padding: 0 10px 4px;
    border-bottom: 1px solid var(--grey);
  }
  .provider__cred {
    font-size: 22px;
    color: var(--green);
    margin-top: 2px;
  }
  .contact-band {
    position: absolute;
    left: 0; top: 0;
    width: 700px; height: 400px;
  }
  .contact {
    position: absolute;
    color: var(--white);
    font-size: 17px;
    text-align: center;
    white-space: nowrap;
  }
  .contact--phone { left: 40px; width: 200px; top: 290px; }
  .contact--email { left: 225px; width: 280px; top: 290px; font-style: italic; }
  .contact--web { left: 480px; width: 200px; top: 290px; }
  .contact--address {
    left: 0; right: 0; top: 345px;
    font-size: 18px;
    display: flex; justify-content: center; align-items: center; gap: 10px;
  }
</style>
</head>
<body>

  <section class="card card--front" aria-label="Card front">
    <div class="brand">
      <span class="brand__mark"></span>
      <span class="brand__name">Tolvera Hearing Center</span>
    </div>
    <p class="front__web">www.tolverahearing.com</p>
  </section>

  <section class="card card--back" aria-label="Card back">
    <div class="brand">
      <span class="brand__mark"></span>
      <span class="brand__name">Tolvera Hearing Center</span>
    </div>
    <div class="provider">
      <p class="provider__name">Peter Wolstenby</p>
      <p class="provider__cred">Au.D. F/NSB</p>
    </div>

    <svg class="contact-band" viewBox="0 0 700 400" aria-hidden="true">
      <defs>
        <linearGradient id="bandFill" x1="0" y1="0" x2="0" y2="1">
          <stop offset="0" stop-color="#7aab3a"/>
          <stop offset="1" stop-color="#5c8f2a"/>
        </linearGradient>
      </defs>
      <rect x="0" y="232" width="700" height="168" fill="url(#bandFill)"/>
      <line x1="0" y1="222" x2="700" y2="222" stroke="#7aab3a" stroke-width="3"/>

      <circle cx="140" cy="222" r="34" fill="#ffffff" stroke="#7aab3a" stroke-width="3"/>
      <circle cx="140" cy="222" r="26" fill="none" stroke="#7aab3a" stroke-width="1.5"/>
      <path d="M131 210c2-2 4-1 5 1l3 5c1 2 0 3-1 4l-2 1c1 3 4 6 7 7l1-2c1-1 2-2 4-1l5 3c2 1 3 3 1 5l-2 2c-3 2-8 1-13-3s-9-10-10-15c0-3 1-5 2-7z" fill="#7aab3a"/>

      <circle cx="365" cy="222" r="34" fill="#ffffff" stroke="#7aab3a" stroke-width="3"/>
      <circle cx="365" cy="222" r="26" fill="none" stroke="#7aab3a" stroke-width="1.5"/>
      <rect x="351" y="213" width="28" height="19" fill="#7aab3a"/>
      <path d="M351 213l14 11 14-11" fill="none" stroke="#ffffff" stroke-width="2"/>

      <circle cx="580" cy="222" r="34" fill="#ffffff" stroke="#7aab3a" stroke-width="3"/>
      <circle cx="580" cy="222" r="26" fill="none" stroke="#7aab3a" stroke-width="1.5"/>
      <g fill="none" stroke="#7aab3a" stroke-width="2">
        <circle cx="580" cy="222" r="13"/>
        <ellipse cx="580" cy="222" rx="6" ry="13"/>
        <line x1="567" y1="222" x2="593" y2="222"/>
        <line x1="569" y1="215" x2="591" y2="215"/>
        <line x1="569" y1="229" x2="591" y2="229"/>
      </g>
    </svg>

    <p class="contact contact--phone">(440) 683-5127</p>
    <p class="contact contact--email">tolverahearing@postvane.com</p>
    <p class="contact contact--web">www.tolverahearing.com</p>
    <p class="contact contact--address">
      <svg width="14" height="20" viewBox="0 0 14 20" aria-hidden="true">
        <path d="M7 0a7 7 0 0 0-7 7c0 5 7 13 7 13s7-8 7-13a7 7 0 0 0-7-7z" fill="#ffffff" opacity="0.85"/>
        <circle cx="7" cy="7" r="2.6" fill="#6a9d32"/>
      </svg>
      837 W. Lindell Ave. Fernbrook, OH 44390
    </p>
  </section>

</body>
</html>
```